Heron Property Inspection business card

I am the principal inspector of Heron Property Inspections. I serve Northern Virginia from Winchester to Arlington.Associate, Federated Guild of Dwelling Examiners (FGDE)Graduate, FGDE Home Inspectors CourseNational Association of Home Inspectors ExamI'd like the business card to look more professional than comical.I pulled the attached picture off the web. I'd like to have something like that or an image of a house as my logo on the cards.

Target Market(s)

Persons who recently purchased a home.

Industry/Entity Type

Business

Contact Information for Business Card

Bob AllenBadger Home Inspections, LLC.4455 River RoadBluemont, Virginia 20135cell: 703-231-6680e-mail: tkmarlow@postvale.net

Font styles to use
Serif
Sans Serif

Requirements
Must have
• I'd like to have a logo, something that identifies me as a home inspector. The attached images are something that I'd like to have incorporated into my business card logo.
Nice to have
• I'd like a sketch of a house and/or a magnifying glass showing a house being inspected. The attached images are used as a suggestion only, I do not own the images.
Should not have
• Gimmicky stuff. I want to appear professional and trustworthy.

```html
<!DOCTYPE html>
<html lang="en">
<head>
<meta charset="utf-8">
<title>Heron Property Inspections – Business Card</title>
<link rel="stylesheet" href="https://fonts.googleapis.com/css2?family=Tinos:wght@400;700&display=swap">
<style>
  :root {
    --backdrop: #e9e7e3;
    --paper: #f7f7f7;
    --brand-blue: #3d4aa8;
    --brand-blue-light: #5361c0;
    --brand-blue-dark: #2f3b94;
    --mark-blue: #3a8fd0;
    --ink-white: #ffffff;
  }
  * { box-sizing: border-box; margin: 0; padding: 0; }
  html, body { width: 1200px; height: 892px; overflow: hidden; }
  body {
    background: var(--backdrop);
    font-family: "Tinos", "Times New Roman", serif;
    position: relative;
  }
  .card {
    position: absolute;
    left: 100px; top: 161px;
    width: 1000px; height: 570px;
    background: var(--paper);
    box-shadow: 0 6px 22px rgba(0,0,0,.18);
    overflow: hidden;
  }
  .card__rule {
    position: absolute; left: 0; right: 0;
    top: 300px; height: 6px;
    background: var(--brand-blue);
  }
  .card__band {
    position: absolute; left: 0; right: 0;
    top: 318px; bottom: 0;
    background: linear-gradient(160deg, var(--brand-blue-light) 0%, var(--brand-blue) 45%, var(--brand-blue-dark) 100%);
  }
  .brand {
    position: absolute; left: 64px; top: 150px;
    display: flex; align-items: center; gap: 22px;
  }
  .brand__dot {
    width: 92px; height: 92px; border-radius: 50%;
    background: var(--mark-blue);
    flex: none;
  }
  .brand__name {
    color: var(--brand-blue-dark);
    font-weight: 400;
    text-transform: uppercase;
    letter-spacing: 2px;
    line-height: 1.05;
  }
  .brand__line--primary { font-size: 42px; display: block; }
  .brand__line--secondary { font-size: 30px; display: block; }
  .person {
    position: absolute; left: 64px; top: 34px;
    color: var(--ink-white);
  }
  .person__name { font-size: 46px; font-weight: 700; letter-spacing: .5px; }
  .person__title { font-size: 22px; margin-left: 150px; margin-top: -2px; }
  .band__line {
    position: absolute; left: 440px; right: 0; top: 118px;
    height: 2px; background: rgba(255,255,255,.85);
  }
  .contact {
    position: absolute; left: 560px; top: 140px;
    list-style: none; color: var(--ink-white);
    font-size: 22px; line-height: 1.55;
  }
</style>
</head>
<body>
  <article class="card">
    <div class="brand">
      <span class="brand__dot" aria-hidden="true"></span>
      <h1 class="brand__name">
        <span class="brand__line--primary">Tim Marlow Heron</span>
        <span class="brand__line--secondary">Property Inspections, LLC</span>
      </h1>
    </div>
    <div class="card__rule"></div>
    <section class="card__band">
      <div class="person">
        <p class="person__name">Employee name</p>
        <p class="person__title">Managing Director</p>
      </div>
      <div class="band__line"></div>
      <ul class="contact">
        <li>703-555-0192</li>
        <li>tkmarlow@postvale.net</li>
        <li>7182 Quarry Lane Fernhill, Virginia 20148</li>
      </ul>
    </section>
  </article>
</body>
</html>
```